Stylish Business Cards Wanted

- DOUBLE SIDED Design Required -

High end, edgy cards for a corporate and personal stylist. Must include logo,
Name: Belinda Harwick
Title: Director and Stylist
telephone : +61 8 7142 5809
email: belinda@theloombriefing.example
website: theloombriefing.example
Tag: Corporate Workwear & Uniform Specialist | Personal Stylist
Would like nice icons for telephone, email, website

Target Market(s)

Businesses wanting stylish uniforms, people wanting stylish wardrobes

Industry/Entity Type

Corporate Workwear Stylist

Contact Information for Business Card

I would like black, white and gold foiling incorporated in the design - possibly a touch of the other colours on my branding guide attached Name: Belinda Harwick Title: Director and Stylist telephone : +61 8 7142 5809 email: belinda@theloombriefing.example website: theloombriefing.example Tag: Corporate Workwear & Uniform Specialist | Personal Stylist Would like nice icons for telephone, email, website

Font styles to use
Other font styles liked:
• Raleway

Colors

Designer to choose colors to be used in the design.

Requirements
Must have
• Gold foil accents

```html
<!DOCTYPE html>
<html lang="en">
<head>
<meta charset="utf-8">
<title>The Loom Briefing – Business Cards</title>
<link rel="stylesheet" href="https://fonts.googleapis.com/css2?family=Raleway:ital,wght@0,400;0,500;0,700;1,400&family=Dancing+Script:wght@500&display=swap">
<style>
  :root {
    --backdrop: #3b3b3c;
    --card-black: #1b1b1d;
    --pattern-grey: #4a4a4d;
    --paper: #f7f7f4;
    --navy: #1b2340;
    --gold: #d9ae3c;
    --gold-light: #efd27a;
    --ink: #2a2a2e;
    --white: #ffffff;
  }
  * { margin: 0; padding: 0; box-sizing: border-box; }
  html, body {
    width: 799px; height: 1200px; overflow: hidden;
    background: var(--backdrop);
  }
  .sheet {
    width: 799px; height: 1200px;
    display: flex; flex-direction: column; align-items: center; justify-content: center;
    gap: 110px;
  }
  .card {
    width: 640px; height: 366px; position: relative; overflow: hidden;
    box-shadow: 0 14px 30px rgba(0,0,0,0.45);
  }

  /* Front */
  .card-front { background: var(--card-black); }
  .front-pattern {
    position: absolute; inset: 0;
    background: radial-gradient(ellipse at 70% 60%, var(--pattern-grey) 0%, #2c2c2f 45%, var(--card-black) 85%);
  }
  .front-brand {
    position: absolute; left: 50%; top: 50%; transform: translate(-50%, -50%);
    font-family: "Raleway", sans-serif; font-weight: 700; font-size: 40px;
    letter-spacing: 1px; color: var(--gold); white-space: nowrap;
    background: var(--card-black); padding: 14px 26px;
  }

  /* Back */
  .card-back { background: var(--paper); }
  .back-brand {
    position: absolute; left: 40px; top: 120px; width: 230px;
    font-family: "Raleway", sans-serif; font-weight: 700; font-size: 36px;
    line-height: 1.1; color: var(--navy);
  }
  .details {
    position: absolute; left: 300px; top: 34px; width: 310px;
    text-align: center; font-family: "Raleway", sans-serif; color: var(--ink);
  }
  .person-name {
    font-family: "Dancing Script", cursive; font-weight: 500; font-size: 30px;
    color: var(--gold); line-height: 1.1;
  }
  .person-title { font-size: 15px; margin-top: 4px; }
  .icon-row {
    display: flex; align-items: center; justify-content: center; gap: 8px;
    margin: 16px 0 12px;
  }
  .icon-row .rule { width: 70px; height: 1px; background: var(--gold); }
  .icon-row svg { width: 18px; height: 18px; }
  .contact-list { list-style: none; font-size: 14.5px; line-height: 1.6; }

  .tagline-band {
    position: absolute; left: 0; right: 0; bottom: 0; height: 66px;
    background: var(--navy); color: var(--white);
    display: flex; align-items: center; justify-content: center;
    font-family: "Raleway", sans-serif; font-style: italic; font-size: 16px;
    letter-spacing: 0.4px;
  }
  .tagline-band .divider { width: 1px; height: 22px; background: var(--white); margin: 0 14px; }
</style>
</head>
<body>
<main class="sheet">

  <section class="card card-front" aria-label="Card front">
    <div class="front-pattern" role="img" aria-label="Repeated embossed brand pattern in dark grey tones"></div>
    <div class="front-brand">The Loom Briefing</div>
  </section>

  <section class="card card-back" aria-label="Card back">
    <div class="back-brand">The Loom Briefing</div>

    <div class="details">
      <p class="person-name">Belinda Harwick</p>
      <p class="person-title">Director and Stylist</p>

      <div class="icon-row">
        <span class="rule"></span>
        <svg viewBox="0 0 20 20" aria-label="Telephone" role="img">
          <circle cx="10" cy="10" r="8.5" fill="none" stroke="var(--gold)" stroke-width="1.4"/>
          <path d="M7 5.8c-.6.4-1 1-.8 1.9.5 2.3 2.6 4.6 5 5.3.9.3 1.6-.1 2-.7l-1.6-1.4-1 .7c-1-.5-1.9-1.4-2.4-2.4l.7-1z" fill="var(--gold)"/>
        </svg>
        <svg viewBox="0 0 20 20" aria-label="Email" role="img">
          <rect x="2.5" y="5" width="15" height="10" fill="none" stroke="var(--gold)" stroke-width="1.4"/>
          <path d="M2.5 5l7.5 6 7.5-6" fill="none" stroke="var(--gold)" stroke-width="1.4"/>
        </svg>
        <svg viewBox="0 0 20 20" aria-label="Website" role="img">
          <circle cx="10" cy="10" r="8" fill="none" stroke="var(--gold)" stroke-width="1.4"/>
          <ellipse cx="10" cy="10" rx="3.5" ry="8" fill="none" stroke="var(--gold)" stroke-width="1.2"/>
          <path d="M2 10h16M3.5 6h13M3.5 14h13" stroke="var(--gold)" stroke-width="1.2"/>
        </svg>
        <span class="rule"></span>
      </div>

      <ul class="contact-list">
        <li>+61 8 7142 5809</li>
        <li>belinda@theloombriefing.example</li>
        <li>www.theloombriefing.example</li>
      </ul>
    </div>

    <div class="tagline-band">
      <span>Corporate Workwear &amp; Uniform Specialist</span>
      <span class="divider"></span>
      <span>Personal Stylist</span>
    </div>
  </section>

</main>
</body>
</html>
```